Investment company needing business card

We are wanting a business card which looks sharp and easy on the eye. We are thinking of having a business card with the logo embossed on it, to really make it stand out. We will only have a small amount of information of the business card, person's name, position, email address and phone number

Contact Information for Business Card

Danielle Frost
Executive Assistant
+64 21 473 5162
danielf@harwickpartners.co.nz

Requirements
Must have
• Embossed logo
Should not have
• Not to be busy

```html
<!DOCTYPE html>
<html lang="en">
<head>
<meta charset="utf-8">
<title>Harwick Partners – Business Card</title>
<link href="https://fonts.googleapis.com/css2?family=Open+Sans:wght@400;700&display=swap" rel="stylesheet">
<style>
  :root {
    --backdrop: #ebe8e5;
    --card: #414042;
    --card-edge: #4a494b;
    --ink-light: #ffffff;
    --ink-muted: #c9c9c9;
    --divider: #555456;
    --accent: #1fb37a;
    --emboss: #5a595b;
  }
  * { margin: 0; padding: 0; box-sizing: border-box; }
  html, body {
    width: 1200px;
    height: 997px;
    overflow: hidden;
    background: var(--backdrop);
    font-family: "Open Sans", Arial, sans-serif;
  }
  .card {
    position: absolute;
    width: 520px;
    height: 297px;
    background: var(--card);
    border-radius: 3px;
    box-shadow: 0 1px 0 var(--card-edge) inset, 0 10px 24px rgba(0,0,0,0.18);
  }
  .card--front { left: 110px; top: 170px; }
  .card--back { left: 570px; top: 530px; }

  .front__brand {
    position: absolute;
    left: 0;
    top: 0;
    width: 230px;
    height: 100%;
    display: flex;
    align-items: center;
    justify-content: center;
    gap: 10px;
  }
  .brand-mark {
    width: 14px;
    height: 14px;
    background: var(--accent);
  }
  .brand-name {
    color: var(--ink-light);
    font-weight: 700;
    font-size: 17px;
    letter-spacing: 1.5px;
    text-transform: uppercase;
  }
  .front__divider {
    position: absolute;
    left: 230px;
    top: 60px;
    width: 1px;
    height: 177px;
    background: var(--divider);
  }
  .front__details {
    position: absolute;
    left: 262px;
    top: 86px;
    color: var(--ink-light);
  }
  .person-name {
    font-weight: 700;
    font-size: 15px;
    letter-spacing: 0.3px;
    text-transform: uppercase;
    line-height: 1.2;
  }
  .person-role {
    font-size: 13px;
    color: var(--ink-muted);
    margin-bottom: 8px;
  }
  .contact-list { list-style: none; }
  .contact-list li {
    display: flex;
    align-items: center;
    gap: 7px;
    font-size: 13px;
    line-height: 1.45;
  }
  .contact-list svg { width: 10px; height: 10px; fill: var(--ink-light); flex: none; }

  .back__brand {
    position: absolute;
    inset: 0;
    display: flex;
    align-items: center;
    justify-content: center;
  }
  .back__brand .brand-name {
    color: var(--emboss);
    font-size: 30px;
    letter-spacing: 3px;
    text-shadow: none;
  }
</style>
</head>
<body>
  <section class="card card--front" aria-label="Business card front">
    <div class="front__brand">
      <span class="brand-mark"></span>
      <span class="brand-name">Harwick Partners</span>
    </div>
    <div class="front__divider"></div>
    <div class="front__details">
      <p class="person-name">Danielle Frost</p>
      <p class="person-role">Executive Assistant</p>
      <ul class="contact-list">
        <li>
          <svg viewBox="0 0 10 10" aria-hidden="true"><path d="M2 0.5 L3.6 2.6 L2.7 3.6 C3.3 5 4.9 6.6 6.4 7.3 L7.4 6.4 L9.5 8 L8.4 9.5 C4.5 9.2 0.8 5.5 0.5 1.6 Z"/></svg>
          <span>+64 21 473 5162</span>
        </li>
        <li>
          <svg viewBox="0 0 10 10" aria-hidden="true"><path d="M0 2 H10 V8.5 H0 Z M0.8 2.6 L5 5.6 L9.2 2.6 V3.4 L5 6.4 L0.8 3.4 Z" fill-rule="evenodd"/></svg>
          <span>danielf@harwickpartners.co.nz</span>
        </li>
        <li>
          <svg viewBox="0 0 10 10" aria-hidden="true"><path d="M5 0.3 A4.7 4.7 0 1 0 5 9.7 A4.7 4.7 0 1 0 5 0.3 Z M5 1.3 A3.7 3.7 0 1 1 5 8.7 A3.7 3.7 0 1 1 5 1.3 Z M4.5 1.3 H5.5 V8.7 H4.5 Z M1.3 4.5 H8.7 V5.5 H1.3 Z" fill-rule="evenodd"/></svg>
          <span>www.harwickpartners.co.nz</span>
        </li>
      </ul>
    </div>
  </section>

  <section class="card card--back" aria-label="Business card back">
    <div class="back__brand">
      <span class="brand-name">Harwick Partners</span>
    </div>
  </section>
</body>
</html>
```